Business card design for my company.
I would like the card's background colour to be black. You can also see our web site to get an idea of our brand. https://www.tmwhomecrafting.com.au/
- Name
- Email

```html
<!DOCTYPE html>
<html lang="en">
<head>
<meta charset="utf-8">
<title>TMW Home Crafting – Business Card</title>
<link href="https://fonts.googleapis.com/css2?family=Arimo:wght@400;700&display=swap" rel="stylesheet">
<style>
  :root {
    --page: #e4e4e4;
    --card: #2e2e2e;
    --green: #0f9444;
    --white: #f2f2f4;
    --rule: #8a8a8a;
  }
  html, body {
    margin: 0;
    width: 1200px;
    height: 1200px;
    overflow: hidden;
    background: var(--page);
    font-family: "Arimo", Arial, sans-serif;
  }
  .card {
    position: absolute;
    width: 664px;
    height: 380px;
    background: var(--card);
    color: var(--white);
  }
  .card-front { left: 257px; top: 153px; }
  .card-back  { left: 253px; top: 631px; }

  .brand {
    position: absolute;
    display: flex;
    align-items: center;
    gap: 12px;
    color: var(--white);
    font-weight: 700;
    letter-spacing: 0.06em;
    white-space: nowrap;
  }
  .brand-mark { background: var(--green); flex: none; }
  .card-front .brand { right: 46px; top: 110px; font-size: 26px; }
  .card-front .brand-mark { width: 22px; height: 22px; }
  .card-back .brand {
    left: 50%; top: 50%;
    transform: translate(-50%, -50%);
    font-size: 46px;
  }
  .card-back .brand-mark { width: 38px; height: 38px; }

  .holder { position: absolute; left: 46px; top: 214px; }
  .holder-name {
    margin: 0;
    color: var(--green);
    font-size: 24px;
    font-weight: 700;
    line-height: 1;
  }
  .holder-role { margin: 6px 0 0; font-size: 15px; line-height: 1; }

  .divider {
    position: absolute;
    left: 47px; right: 46px; top: 271px;
    height: 1px;
    background: var(--rule);
  }

  .contact-list {
    position: absolute;
    left: 44px; top: 282px;
    margin: 0; padding: 0;
    list-style: none;
    font-size: 16px;
  }
  .contact-list li {
    display: flex;
    align-items: center;
    gap: 10px;
    height: 20px;
  }
  .contact-list svg { width: 14px; height: 14px; fill: var(--green); flex: none; }

  .address {
    position: absolute;
    right: 42px; top: 284px;
    margin: 0;
    text-align: right;
    font-size: 16px;
    font-style: normal;
    line-height: 20px;
  }
</style>
</head>
<body>
  <section class="card card-front">
    <div class="brand"><span class="brand-mark"></span>TMW HOME CRAFTING</div>

    <div class="holder">
      <p class="holder-name">DANIEL REEVE</p>
      <p class="holder-role">President</p>
    </div>

    <div class="divider"></div>

    <ul class="contact-list">
      <li>
        <svg viewBox="0 0 24 24" aria-hidden="true"><path d="M6.6 10.8a15.2 15.2 0 0 0 6.6 6.6l2.2-2.2a1 1 0 0 1 1-.25 11.4 11.4 0 0 0 3.6.57 1 1 0 0 1 1 1V20a1 1 0 0 1-1 1A17 17 0 0 1 3 4a1 1 0 0 1 1-1h3.5a1 1 0 0 1 1 1c0 1.25.2 2.45.57 3.6a1 1 0 0 1-.25 1z"/></svg>
        555-210-4418
      </li>
      <li>
        <svg viewBox="0 0 24 24" aria-hidden="true"><path d="M7 1h10a2 2 0 0 1 2 2v18a2 2 0 0 1-2 2H7a2 2 0 0 1-2-2V3a2 2 0 0 1 2-2zm0 3v15h10V4zm5 16.2a.9.9 0 1 0 0 1.8.9.9 0 0 0 0-1.8z"/></svg>
        555-210-7720
      </li>
      <li>
        <svg viewBox="0 0 24 24" aria-hidden="true"><path d="M2 5h20v14H2zm2 2v.5l8 5.5 8-5.5V7zm0 3v7h16v-7l-8 5.5z"/></svg>
        hello@tmwhome.com
      </li>
    </ul>

    <address class="address">
      42 Wattle Grove<br>
      Fernvale, Australia 4012<br>
      www.tmwhome.com
    </address>
  </section>

  <section class="card card-back">
    <div class="brand"><span class="brand-mark"></span>TMW HOME CRAFTING</div>
  </section>
</body>
</html>
```